Build Website for Playful Brand that helps content creators build businesses

Please help me create a website for my Cobalt that helps content creators build businesses around their audience. I have attached a Draftly and vibe that I am going for at mossquay.io.

Open for changes, but I want to keep the colour I currently have (a light teal). Ultimately the brand is playful but should come off as a very modern elevated brand.

I am looking for a few pages including

1. Home (with clear CTA button)
A section where I can input what the Cobalt does, and some brands that we have launched

2. About Me
A simple page, that has preferably able to put a circular image of myself and then give a quick background about the Cobalt

3. Blog (can you include how blog posts will appear and it should sit nicely in the page)
This ideally is a section that will be able to link to another software so my blogs automatically flow into here or posts. But otherwise it should have sections of blocks where creators can see about topics that I post about

4. Contact (this should include a form that will allow users to contact me)
Finally a contact page where it links my socials, similar what is there, but ideally there is a form they can fill out which I can link to my inbox as well. This should be a simple page as well

Create a multi page website, including a page that will link or can link blog post

Similar to this vibe and logo - https://mossquay.io/

Target Marketa(s)

Content Creators

Coding

Coded - Draftly and coding required

Number of Pages Required

4 page

Requirements
Must have
• Home, Contact Me (Including a place to submit an enquiry and form), Blog Post Page As well

```html
<!DOCTYPE html>
<html lang="en">
<head>
<meta charset="UTF-8">
<title>Moss Quay — Building Businesses</title>
<link href="https://fonts.googleapis.com/css2?family=Lexend:wght@500;600&family=Poppins:wght@400;500;600&display=swap" rel="stylesheet">
<style>
:root{
  --ink:#3e5a62;
  --ink-dark:#344c53;
  --teal:#7fb4c2;
  --sky:#b9e3ee;
  --sky-light:#d4eef5;
  --grey:#c3cacc;
  --text:#2f3b3f;
  --white:#ffffff;
  --star:#f2c21b;
}
*{margin:0;padding:0;box-sizing:border-box}
html,body{width:1200px;height:3561px;overflow:hidden;background:var(--white)}
body{position:relative;font-family:"Poppins",sans-serif;color:var(--text)}
.abs{position:absolute}
.heading{font-family:"Lexend",sans-serif;font-weight:600;letter-spacing:1.5px;color:var(--ink)}
/* top bar */
.topbar{left:0;top:0;width:1200px;height:55px;background:var(--ink);color:var(--white);font-size:14px}
.topbar .item{top:0;height:55px;display:flex;align-items:center;gap:18px}
.ic{width:30px;height:30px;border-radius:50%;background:rgba(255,255,255,.12);display:flex;align-items:center;justify-content:center}
.divider{left:430px;top:6px;width:1px;height:43px;background:rgba(255,255,255,.25)}
.follow{right:110px;top:0;height:55px;display:flex;align-items:center;font-size:13px;color:#b8c6ca}
.social{width:34px;height:34px;border-radius:50%;background:var(--white)}
/* nav */
.nav{left:0;top:55px;width:1200px;height:105px;background:var(--white);border-bottom:1px solid #e3e8ea}
.logo-word{font-family:"Poppins",sans-serif;font-weight:500;letter-spacing:2px;color:var(--ink)}
.menu{right:113px;top:0;height:105px;display:flex;align-items:center;gap:31px;font-size:16px;font-weight:500;color:#222}
.menu .active{color:var(--teal)}
/* hero */
.hero-title{left:110px;top:236px;font-size:41px;color:var(--white)}
.hero-text{left:110px;top:312px;width:480px;color:var(--white);font-size:18px;line-height:46px}
.btn-light{left:111px;top:476px;width:185px;height:55px;background:var(--white);border-radius:4px;display:flex;align-items:center;justify-content:center;font-family:"Lexend",sans-serif;font-weight:600;font-size:21px;letter-spacing:1px;color:var(--ink);box-shadow:0 3px 8px rgba(0,0,0,.15)}
/* brands */
.section-title{width:1200px;left:0;text-align:center;font-size:35px}
.brands{left:118px;top:888px;width:964px;height:259px;display:grid;grid-template-columns:repeat(5,1fr);grid-template-rows:1fr 1fr}
.brand{display:flex;align-items:center;justify-content:center;gap:8px;font-size:26px;font-weight:500;color:#333;border-right:1px solid #dfe3e4}
.brand:nth-child(5n){border-right:none}
.brand:nth-child(-n+5){border-bottom:1px solid #dfe3e4}
.brand .dot{width:22px;height:22px;border-radius:50%;background:var(--teal)}
/* about */
.circle{border-radius:50%}
.about-title{left:608px;top:1232px;font-size:35px}
.about-text{left:608px;top:1305px;width:490px;font-size:16.5px;line-height:38.5px;color:#333}
.btn-dark{background:var(--ink);color:var(--white);border-radius:4px;display:flex;align-items:center;justify-content:center;font-family:"Lexend",sans-serif;font-weight:600;letter-spacing:1px;box-shadow:6px 6px 0 #d6dcde}
/* blogs */
.blog-band{left:0;top:1759px;width:1200px;height:400px;background:var(--sky)}
.card{top:1917px;width:320px;height:441px;border-radius:8px;overflow:hidden;background:linear-gradient(180deg,#6d7b80 0%,#8a8078 35%,#3f3a38 72%,#0d0d0d 100%);color:var(--white)}
.tag{left:27px;top:28px;padding:0 8px;height:40px;display:flex;align-items:center;background:var(--ink);font-family:"Lexend",sans-serif;font-weight:600;font-size:18px;letter-spacing:1px}
.card .date{left:25px;top:271px;font-family:"Lexend",sans-serif;font-size:17px;font-weight:500}
.card .ttl{left:25px;top:310px;font-size:17px;font-weight:500}
.card .ex{left:25px;top:350px;width:280px;font-size:14px;line-height:33px}
/* testimonials */
.quote{left:230px;top:2500px;width:740px;text-align:center;font-size:17px;line-height:38.5px;color:#333}
.arrow{width:28px;height:28px;border-radius:50%;display:flex;align-items:center;justify-content:center}
/* contact card */
.contact-card{left:636px;top:2862px;width:429px;height:569px;background:var(--white);box-shadow:0 4px 18px rgba(0,0,0,.12);border-radius:4px}
.label{font-size:14px;font-weight:500;color:#222}
.field{border:1.5px solid var(--ink);border-radius:6px;height:44px;background:var(--white)}
/* footer */
.foot-h{font-size:21px;color:var(--white);letter-spacing:1px}
.foot-link{font-size:16px;color:var(--white)}
.bottombar{left:0;top:3490px;width:1200px;height:71px;background:var(--ink-dark);color:var(--white);font-size:16px}
</style>
</head>
<body>

<!-- top bar -->
<div class="abs topbar">
  <div class="abs item" style="left:113px">
    <span class="ic"><svg width="14" height="10" viewBox="0 0 14 10"><rect x="0.5" y="0.5" width="13" height="9" rx="1" fill="none" stroke="#fff"/><path d="M1 1l6 5 6-5" fill="none" stroke="#fff"/></svg></span>
    <span>EMAIL US : HELLO@MOSSQUAY.IO</span>
  </div>
  <div class="abs divider"></div>
  <div class="abs item" style="left:472px">
    <span class="ic"><svg width="13" height="13" viewBox="0 0 24 24"><path fill="#fff" d="M6.6 10.8a15 15 0 006.6 6.6l2.2-2.2a1 1 0 011-.25 11.4 11.4 0 003.6.6 1 1 0 011 1V20a1 1 0 01-1 1A17 17 0 013 4a1 1 0 011-1h3.5a1 1 0 011 1c0 1.25.2 2.45.6 3.6a1 1 0 01-.25 1z"/></svg></span>
    <span>CALL US : +1 555 010 0199</span>
  </div>
  <div class="abs follow"><span style="margin-right:14px">FOLLOW US :</span><span class="social" aria-label="Social profile"></span><span class="social" style="margin-left:10px" aria-label="Social profile"></span></div>
</div>

<!-- nav -->
<div class="abs nav">
  <div class="abs" style="left:125px;top:18px;width:60px;height:40px;border-radius:50%;background:var(--sky)"></div>
  <div class="abs logo-word" style="left:110px;top:78px;font-size:15px">MOSS QUAY</div>
  <div class="abs menu">
    <span class="active">HOME</span><span>ABOUT US</span><span>BLOGS</span><span>TESTIMONIALS</span><span>BRANDS</span><span>CONTACT US</span>
  </div>
</div>

<!-- hero -->
<svg class="abs" style="left:0;top:160px" width="1200" height="566" viewBox="0 0 1200 566">
  <defs><linearGradient id="heroGrad" x1="0" y1="0" x2="1" y2="0.4"><stop offset="0" stop-color="#3e5a62"/><stop offset="0.55" stop-color="#5f8891"/><stop offset="1" stop-color="#b3dbe4"/></linearGradient></defs>
  <path d="M0 0H1200V80C1020 230 800 560 470 566C310 570 170 505 70 430L0 360Z" fill="url(#heroGrad)"/>
</svg>
<h1 class="abs heading hero-title" style="color:#fff">BUILDING BUSINESSES</h1>
<p class="abs hero-text">Helping Content Creators Build Their Own Brand<br>Founded in 2024, we provide the highest level of<br>goods and service.</p>
<div class="abs btn-light">GET STARTED</div>
<svg class="abs" style="left:581px;top:242px" width="507" height="484" viewBox="0 0 507 484" role="img" aria-label="Photo of two colleagues discussing work at a laptop">
  <defs><linearGradient id="photoGrad" x1="0" y1="0" x2="1" y2="1"><stop offset="0" stop-color="#b7c3c6"/><stop offset="0.5" stop-color="#8a7461"/><stop offset="1" stop-color="#3a3633"/></linearGradient></defs>
  <path d="M120 40Q150 0 200 0H340Q380 0 410 40L495 190Q515 230 495 270L420 430Q395 484 340 484H160Q110 484 85 440L10 290Q-10 250 10 210Z" fill="url(#photoGrad)"/>
</svg>

<!-- brands -->
<h2 class="abs heading section-title" style="top:798px">OUR BRANDS</h2>
<div class="abs brands">
  <div class="brand"><span class="dot"></span>Nexa</div>
  <div class="brand">Brightfold</div>
  <div class="brand"><span class="dot"></span>Draftly</div>
  <div class="brand">Inventra</div>
  <div class="brand">Sprout</div>
  <div class="brand"><span class="dot"></span>Cobalt</div>
  <div class="brand">Olio</div>
  <div class="brand">Marketa</div>
  <div class="brand">Crestly</div>
  <div class="brand"><span class="dot"></span>Lumora</div>
</div>

<!-- about -->
<div class="abs circle" style="left:111px;top:1227px;width:194px;height:194px;background:linear-gradient(135deg,#cfd6d8,#7a8a8e)" role="img" aria-label="Photo of a team meeting in a bright office"></div>
<div class="abs circle" style="left:411px;top:1289px;width:138px;height:138px;background:linear-gradient(135deg,#a79c8f,#5b5048)" role="img" aria-label="Photo of colleagues working at laptops"></div>
<div class="abs circle" style="left:113px;top:1488px;width:120px;height:120px;background:linear-gradient(135deg,#e2e4e4,#6c7478)" role="img" aria-label="Photo of a presenter speaking to a group"></div>
<div class="abs circle" style="left:283px;top:1490px;width:188px;height:188px;background:#4f6c74;border:3px solid var(--ink);display:flex;align-items:center;justify-content:center">
  <svg width="80" height="70" viewBox="0 0 80 70" fill="none" stroke="#fff" stroke-width="3" stroke-linejoin="round"><rect x="10" y="12" width="60" height="44" rx="5"/><path d="M30 12V5h20v7"/><path d="M18 40l12-10 10 8 10-8 12 10"/></svg>
</div>
<div class="abs circle" style="left:349px;top:1240px;width:34px;height:34px;background:var(--grey)"></div>
<div class="abs circle" style="left:106px;top:1442px;width:34px;height:34px;background:var(--grey)"></div>
<div class="abs circle" style="left:255px;top:1456px;width:32px;height:32px;background:var(--sky-light)"></div>
<div class="abs circle" style="left:509px;top:1532px;width:32px;height:32px;background:var(--sky-light)"></div>
<h2 class="abs heading about-title">ABOUT US</h2>
<p class="abs about-text">Lorem ipsum dolor sit amet, consectetur adipiscing elit, sed do eiusmod tempor incididunt ut labore et dolore magna aliqua.<br>Lorem ipsum dolor sit amet, consectetur adipiscing elit, sed do eiusmod tempor incididunt ut labore et dolore magna aliqua. Ut enim ad minim veniam, quis nostrud exercitation ullamco laboris nisi ut aliquip ex ea commodo consequat.</p>
<div class="abs btn-dark" style="left:608px;top:1580px;width:184px;height:56px;font-size:21px">LEARN MORE</div>

<!-- blogs -->
<div class="abs blog-band"></div>
<h2 class="abs heading" style="left:110px;top:1820px;font-size:35px">LATEST BLOGS</h2>
<div class="abs" style="left:960px;top:1828px;display:flex;align-items:center;gap:12px">
  <span class="heading" style="font-size:19px;text-decoration:underline">VIEW ALL</span>
  <span class="arrow" style="width:20px;height:20px;background:var(--ink)"><svg width="8" height="10" viewBox="0 0 8 10"><path d="M2 1l4 4-4 4" stroke="#fff" stroke-width="2" fill="none"/></svg></span>
</div>
<div class="abs card" style="left:111px" role="img" aria-label="Blog cover photo of two smiling colleagues">
  <div class="abs tag">LOREM LIPSUM</div><div class="abs date">23RD JUNE 2024</div><div class="abs ttl">LOREM IPSUM DOLOR SIT AMET</div><div class="abs ex">Lorem ipsum dolor sit amet, consectetur adipiscing elit</div>
</div>
<div class="abs card" style="left:440px" role="img" aria-label="Blog cover photo of two smiling colleagues">
  <div class="abs tag">LOREM LIPSUM</div><div class="abs date">23RD JUNE 2024</div><div class="abs ttl">LOREM IPSUM DOLOR SIT AMET</div><div class="abs ex">Lorem ipsum dolor sit amet, consectetur adipiscing elit</div>
</div>
<div class="abs card" style="left:769px" role="img" aria-label="Blog cover photo of two smiling colleagues">
  <div class="abs tag">LOREM LIPSUM</div><div class="abs date">23RD JUNE 2024</div><div class="abs ttl">LOREM IPSUM DOLOR SIT AMET</div><div class="abs ex">Lorem ipsum dolor sit amet, consectetur adipiscing elit</div>
</div>

<!-- testimonials -->
<h2 class="abs heading section-title" style="top:2430px">OUR TESTIMONIALS</h2>
<p class="abs quote">Lorem ipsum dolor sit amet, consectetur adipiscing elit, sed do eiusmod tempor incididunt ut labore et dolore magna aliqua. Ut enim ad minim veniam, quis nostrud exercitation ullamco laboris nisi ut aliquip ex ea commodo consequat.</p>
<div class="abs arrow" style="left:113px;top:2564px;background:#111"><svg width="10" height="12" viewBox="0 0 10 12"><path d="M7 1L2 6l5 5" stroke="#fff" stroke-width="2.2" fill="none"/></svg></div>
<div class="abs arrow" style="left:1057px;top:2564px;background:var(--ink)"><svg width="10" height="12" viewBox="0 0 10 12"><path d="M3 1l5 5-5 5" stroke="#fff" stroke-width="2.2" fill="none"/></svg></div>
<svg class="abs" style="left:536px;top:2636px" width="128" height="26" viewBox="0 0 128 26">
  <defs><path id="star" d="M12 1l3.2 7 7.6.8-5.7 5.1 1.6 7.5L12 17.6 5.3 21.4l1.6-7.5L1.2 8.8 8.8 8z"/></defs>
  <use href="#star" fill="#f2c21b"/><use href="#star" x="26" fill="#f2c21b"/><use href="#star" x="52" fill="#f2c21b"/><use href="#star" x="78" fill="#f2c21b"/><use href="#star" x="104" fill="#f2c21b"/>
</svg>
<div class="abs circle" style="left:466px;top:2699px;width:82px;height:82px;background:linear-gradient(180deg,#e6e9ea,#7ba3c9)" role="img" aria-label="Portrait of the reviewer"></div>
<div class="abs" style="left:586px;top:2708px;font-size:20px;font-weight:500;line-height:36px;color:var(--ink);letter-spacing:.5px">LOREM LIPSUM<br>MANAGER</div>

<!-- footer -->
<svg class="abs" style="left:0;top:2920px" width="1200" height="570" viewBox="0 0 1200 570">
  <path d="M0 245C20 160 70 110 160 90L540 10C580 0 610 15 630 40L1200 460V570H0Z" fill="var(--ink)"/>
</svg>
<div class="abs" style="left:165px;top:3050px;width:90px;height:64px;border-radius:50%;background:var(--sky)"></div>
<div class="abs logo-word" style="left:113px;top:3135px;font-size:23px;color:#fff;letter-spacing:3px;font-weight:400">MOSS QUAY</div>
<div class="abs heading foot-h" style="left:114px;top:3205px">QUICK LINKS</div>
<div class="abs heading foot-h" style="left:319px;top:3205px">OTHER LINKS</div>
<div class="abs foot-link" style="left:115px;top:3256px;line-height:42px">HOME<br>ABOUT US<br>BLOG<br>CONTACT</div>
<div class="abs foot-link" style="left:320px;top:3256px;line-height:42px">PRIVACY POLICY<br>TERMS OF USE<br>SITE MAP<br>SERVICES</div>

<!-- contact form -->
<div class="abs contact-card">
  <h2 class="abs heading" style="left:0;width:429px;text-align:center;top:40px;font-size:35px">CONTACT US</h2>
  <div class="abs label" style="left:21px;top:128px">FIRST NAME</div>
  <div class="abs label" style="left:223px;top:128px">LAST NAME</div>
  <div class="abs field" style="left:21px;top:146px;width:185px"></div>
  <div class="abs field" style="left:223px;top:146px;width:185px"></div>
  <div class="abs label" style="left:21px;top:228px">EMAIL ADDRESS</div>
  <div class="abs label" style="left:223px;top:228px">PHONE NUMBER</div>
  <div class="abs field" style="left:21px;top:246px;width:185px"></div>
  <div class="abs field" style="left:223px;top:246px;width:185px"></div>
  <div class="abs label" style="left:21px;top:324px">MESSAGE</div>
  <div class="abs field" style="left:21px;top:343px;width:386px;height:78px"></div>
  <div class="abs btn-dark" style="left:134px;top:464px;width:157px;height:47px;font-size:18px">CONTACT ME</div>
</div>

<!-- bottom bar -->
<div class="abs bottombar">
  <div class="abs" style="left:112px;top:0;height:71px;display:flex;align-items:center">© 2024. ALL RIGHTS RESERVED.</div>
  <div class="abs" style="right:111px;top:0;height:71px;display:flex;align-items:center;gap:10px"><span class="social" aria-label="Social profile"></span><span class="social" aria-label="Social profile"></span></div>
</div>

</body>
</html>
```